Sparkling Wine Label Mirren Hollow

Super Premium Sparkling Wine Label

We are a super premium tasmanian fine wine producer and are about to release our first Sparking Wine.

please visit www.mirrenhollow-example.com.au to check out our range of wine. We need a label that will sit within this branding but as the aspirational product. We think that the Vosse grey/navy label will fit into this concept. It is masculine clean elegent and very smick,
and would be a great addition to our line see Argent Pinot Noir label.

However you can be quite creative with Sparkling Line eg Belvane Royal Cuvee is a stunning classical french label featuring gold baroque detail and feminine elegence.

Its up to you if you where spending $50 on a special bottles of sparkling wine what would you expect to see?

Black/Gold Graphite/Gold

Needs a neck /collar label

Main Front Label
Mirren Hollow
Chardonnay Pinot Noir
Tasmania

Back label has all the techical into you can use the back label from existing labels but reverserve out the colours to black and white or graphite and white

We want a label that oozes quality and expense. That says this the way I want to celebrate.

Target Market(s)

40 60 age group appreciator of quality

Industry/Entity Type

Product

Requirements
Must have
• Neck label
Simular to Vosse Shield so
MIRREN arched above
G rondel in middle possibiliy replacing coat of arms
TASMANIA arched under in red

Main Front Label
Mirren Hollow
Tasmania
Chardonnay Pinot Noir 750ML

Back Label / use the attachment Mirren label just reverse out so that it is a black label with white writing and amend information
Mirren Hollow
23 Pell Morrow Rd Ashvale
Tasmania, 7261
0412557390
www.mirrenhollow-example.com.au
contact@mirrenhollow-example.com.au
Sulphur Dioxide Added
Alc/Vol 12.5%
7.7 Standard Drinks

Rondel g

```html
<!DOCTYPE html>
<html lang="en">
<head>
<meta charset="utf-8">
<title>Mirren Hollow Sparkling – Label Set</title>
<link rel="stylesheet" href="https://fonts.googleapis.com/css2?family=Pinyon+Script&family=Cinzel:wght@600&family=EB+Garamond:ital@0;1&family=Open+Sans:wght@400&display=swap">
<style>
  :root{
    --backdrop:#2e2f33;
    --foil:#e6e6ee;
    --foil-shade:#d3d4de;
    --paper:#f1f1f5;
    --frame:#a9abb3;
    --ink:#2a2a2e;
    --ink-soft:#55565c;
    --accent-red:#c8202a;
    --map-tone:#e2e3ea;
  }
  *{margin:0;padding:0;box-sizing:border-box}
  html,body{width:1200px;height:1133px;overflow:hidden;background:var(--backdrop)}
  .canvas{position:relative;width:1200px;height:1133px}
  .capsule{position:absolute;top:60px;width:300px;height:500px}
  .capsule--front{left:230px}
  .capsule--back{left:676px}
  .capsule svg{width:300px;height:500px;display:block}
  .neck-script{font-family:"Pinyon Script",cursive;font-size:64px;fill:var(--ink)}
  .shield-arch{font-family:"Cinzel",serif;font-size:22px;fill:var(--ink);letter-spacing:2px}
  .shield-region{font-family:"EB Garamond",serif;font-size:11px;fill:var(--accent-red);letter-spacing:1px}
  .shield-name{font-family:"EB Garamond",serif;font-size:9px;fill:var(--ink)}

  .label{position:absolute;top:810px;width:234px;height:200px;background:var(--paper);
    border:2px solid var(--frame);outline:1px solid var(--frame);outline-offset:-6px}
  .label--front{left:264px}
  .label--back{left:728px}

  .front-name{position:absolute;left:0;right:0;top:8px;text-align:center;
    font-family:"Pinyon Script",cursive;font-size:72px;line-height:1;color:var(--ink)}
  .front-sub{position:absolute;left:0;right:0;top:92px;text-align:center;padding-left:30px;
    font-family:"Open Sans",sans-serif;font-size:15px;letter-spacing:1px;color:var(--ink-soft)}
  .front-variety{position:absolute;left:0;right:0;top:134px;text-align:center;
    font-family:"Pinyon Script",cursive;font-size:20px;color:var(--ink)}
  .front-foot{position:absolute;left:18px;right:18px;bottom:10px;display:flex;justify-content:space-between;
    font-family:"EB Garamond",serif;font-size:14px;color:var(--ink)}

  .back-info{position:absolute;left:14px;top:12px;width:124px;white-space:nowrap;
    font-family:"Open Sans",sans-serif;font-size:5.8px;line-height:8.4px;color:var(--ink)}
  .back-map{position:absolute;right:10px;top:10px;width:76px;height:170px;
    background:linear-gradient(180deg,var(--map-tone),#d7d8e0)}
  .back-seal{position:absolute;left:14px;top:114px;width:60px;height:60px;display:flex;
    align-items:center;justify-content:center}
  .back-seal .ring{position:absolute;inset:0;border:1px solid var(--ink-soft);border-radius:50%}
  .back-seal span{font-family:"EB Garamond",serif;font-size:10px;color:var(--ink)}
  .back-origin{position:absolute;left:14px;bottom:8px;font-family:"EB Garamond",serif;
    font-size:9px;color:var(--ink)}
</style>
</head>
<body>
<main class="canvas">

  <div class="capsule capsule--front">
    <svg viewBox="0 0 300 500" aria-label="Neck and collar label">
      <defs>
        <linearGradient id="foilFront" x1="0" x2="1">
          <stop offset="0" stop-color="var(--foil-shade)"/>
          <stop offset=".5" stop-color="var(--foil)"/>
          <stop offset="1" stop-color="var(--foil-shade)"/>
        </linearGradient>
        <path id="archTopA" d="M88 440 A62 62 0 0 1 212 440"/>
        <path id="archLowA" d="M112 436 A38 38 0 0 0 188 436"/>
      </defs>
      <path class="neck-band" d="M95 0 L205 0 L210 330 Q214 360 228 372 L72 372 Q86 360 90 330 Z" fill="url(#foilFront)"/>
      <text class="neck-script" transform="translate(130 90) rotate(90)">Mirren</text>
      <path class="collar" d="M42 410 Q80 372 150 366 Q220 372 258 410 L262 448 L212 450 Q172 460 150 494 Q128 460 88 450 L38 448 Z" fill="url(#foilFront)"/>
      <text class="shield-arch"><textPath href="#archTopA" startOffset="50%" text-anchor="middle">MIRREN</textPath></text>
      <circle cx="150" cy="436" r="24" fill="none" stroke="var(--ink-soft)" stroke-width="1"/>
      <text class="shield-name" x="150" y="439" text-anchor="middle">Mirren</text>
      <text class="shield-region"><textPath href="#archLowA" startOffset="50%" text-anchor="middle">TASMANIA</textPath></text>
    </svg>
  </div>

  <div class="capsule capsule--back">
    <svg viewBox="0 0 300 500" aria-label="Neck and collar label">
      <defs>
        <linearGradient id="foilBack" x1="0" x2="1">
          <stop offset="0" stop-color="var(--foil-shade)"/>
          <stop offset=".5" stop-color="var(--foil)"/>
          <stop offset="1" stop-color="var(--foil-shade)"/>
        </linearGradient>
        <path id="archTopB" d="M88 440 A62 62 0 0 1 212 440"/>
        <path id="archLowB" d="M112 436 A38 38 0 0 0 188 436"/>
      </defs>
      <path class="neck-band" d="M95 0 L205 0 L210 330 Q214 360 228 372 L72 372 Q86 360 90 330 Z" fill="url(#foilBack)"/>
      <path class="collar" d="M42 410 Q80 372 150 366 Q220 372 258 410 L262 448 L212 450 Q172 460 150 494 Q128 460 88 450 L38 448 Z" fill="url(#foilBack)"/>
      <text class="shield-arch"><textPath href="#archTopB" startOffset="50%" text-anchor="middle">MIRREN</textPath></text>
      <circle cx="150" cy="436" r="24" fill="none" stroke="var(--ink-soft)" stroke-width="1"/>
      <text class="shield-name" x="150" y="439" text-anchor="middle">Mirren</text>
      <text class="shield-region"><textPath href="#archLowB" startOffset="50%" text-anchor="middle">TASMANIA</textPath></text>
    </svg>
  </div>

  <section class="label label--front">
    <div class="front-name">Mirren</div>
    <div class="front-sub">HOLLOW</div>
    <div class="front-variety">Chardonnay Pinot Noir</div>
    <div class="front-foot"><span>750ml</span><span>Tasmania</span></div>
  </section>

  <section class="label label--back">
    <div class="back-info">
      Mirren Hollow<br>
      23 Pell Morrow Road Ashvale<br>
      Tasmania Australia 7261<br>
      0412 557 390<br>
      contact@mirrenhollow-example.com.au<br>
      www.mirrenhollow-example.com.au<br>
      Alc/Vol 12.5&nbsp; Standard drinks 8<br>
      Sulphur Dioxide&nbsp; added<br>
      7.7 Standard Drinks
    </div>
    <div class="back-map" role="img" aria-label="Map of the Tasmanian east coast showing the estate location"></div>
    <div class="back-seal"><div class="ring"></div><span>Mirren</span></div>
    <div class="back-origin">Wine of Australia</div>
  </section>

</main>
</body>
</html>
```